QVR business card

Need a business card for a company that provides instructional design and elearning development services. The website is here: http://quorvane.studio/

I'm attaching a current logo, as well as the old business card design. While I like to keep it clean, the old design is too simplistic for my liking. The only idea I want to reuse from the old design is placing industry jargon on the back of the card, just need a better way to present it. But if you have other ideas for the back--feel free to experiment.

Please use the colors complementary to the color we have on the website. Thank you!

```html
<!DOCTYPE html>
<html lang="en">
<head>
<meta charset="utf-8">
<title>QVR business card</title>
<link rel="stylesheet" href="https://fonts.googleapis.com/css2?family=Ubuntu:wght@400;500&family=Encode+Sans+Condensed:wght@300;400;700&family=Open+Sans:wght@300;400&display=swap">
<style>
  :root {
    --backdrop: #8c8c8c;
    --card-white: #f1f1f0;
    --brand-teal: #1aa19f;
    --brand-gold: #bcaa6c;
    --ink: #3a3a3a;
    --jargon: #e4e8e8;
  }
  * { margin: 0; padding: 0; box-sizing: border-box; }
  html, body { width: 1105px; height: 1200px; overflow: hidden; }
  body { background: var(--backdrop); position: relative; font-family: "Ubuntu", sans-serif; }

  .card { position: absolute; left: 182px; width: 747px; height: 426px; overflow: hidden; }
  .card-front { top: 119px; background: var(--card-white); }
  .card-back { top: 636px; background: var(--brand-teal); }

  .brand-name {
    position: absolute; left: 48px; top: 58px;
    font-family: "Ubuntu", sans-serif; font-weight: 500;
    font-size: 52px; letter-spacing: 3px; color: var(--brand-gold);
  }

  .holder { position: absolute; left: 48px; top: 286px; }
  .holder-name { font-size: 23px; color: var(--brand-teal); line-height: 30px; }
  .holder-role { font-size: 19px; color: var(--brand-gold); line-height: 26px; }

  .contact-list { position: absolute; left: 384px; top: 287px; list-style: none; }
  .contact-item {
    display: flex; align-items: center; gap: 10px;
    font-size: 18px; color: var(--ink); line-height: 29.5px;
  }
  .contact-icon { width: 17px; height: 17px; fill: var(--brand-teal); flex: none; }

  .jargon { position: absolute; inset: 0; width: 747px; height: 426px; }
  .jargon text { fill: var(--jargon); text-transform: uppercase; }
  .cond-bold { font-family: "Encode Sans Condensed", sans-serif; font-weight: 700; }
  .cond-regular { font-family: "Encode Sans Condensed", sans-serif; font-weight: 400; }
  .cond-light { font-family: "Encode Sans Condensed", sans-serif; font-weight: 300; }
  .wide-light { font-family: "Open Sans", sans-serif; font-weight: 300; }
  .wide-regular { font-family: "Open Sans", sans-serif; font-weight: 400; }
</style>
</head>
<body>

<section class="card card-front" aria-label="Business card front">
  <div class="brand-name">QVR</div>

  <div class="holder">
    <p class="holder-name">Marten Kolvaro</p>
    <p class="holder-role">CEO/Founder</p>
  </div>

  <ul class="contact-list">
    <li class="contact-item">
      <svg class="contact-icon" viewBox="0 0 24 24" aria-hidden="true"><path d="M6.6 10.8a15.1 15.1 0 0 0 6.6 6.6l2.2-2.2a1 1 0 0 1 1-.25 11.4 11.4 0 0 0 3.6.57 1 1 0 0 1 1 1V20a1 1 0 0 1-1 1A17 17 0 0 1 3 4a1 1 0 0 1 1-1h3.5a1 1 0 0 1 1 1c0 1.25.2 2.45.57 3.57a1 1 0 0 1-.25 1z"/></svg>
      555-013-4827
    </li>
    <li class="contact-item">
      <svg class="contact-icon" viewBox="0 0 24 24" aria-hidden="true"><path d="M2 5h20v14H2z M3.5 6.5v.4L12 12.5l8.5-5.6v-.4z" fill-rule="evenodd"/></svg>
      mkolvaro@quorvane.studio
    </li>
    <li class="contact-item">
      <svg class="contact-icon" viewBox="0 0 24 24" aria-hidden="true"><circle cx="12" cy="12" r="10"/><path d="M8 6c2 1 1 3 3 3s1 3-1 4-1 4-3 3M15 15c1-1 3-1 4 1" stroke="#f1f1f0" stroke-width="1.6" fill="none"/></svg>
      www.quorvane.studio
    </li>
  </ul>
</section>

<section class="card card-back" aria-label="Business card back">
  <svg class="jargon" viewBox="0 0 747 426" role="img" aria-label="Learning design terms">
    <text class="cond-bold" x="12" y="40" font-size="38" textLength="250" lengthAdjust="spacingAndGlyphs">Storyboarding</text>
    <text class="cond-light" x="274" y="40" font-size="38" textLength="460" lengthAdjust="spacingAndGlyphs">Needs Analysis Microlearning</text>

    <text class="wide-light" x="12" y="96" font-size="48" textLength="720" lengthAdjust="spacingAndGlyphs">Course Design &amp; Delivery</text>

    <text class="wide-regular" x="12" y="164" font-size="62" textLength="720" lengthAdjust="spacingAndGlyphs">Let's build it together</text>

    <text class="cond-bold" x="12" y="214" font-size="38" textLength="300" lengthAdjust="spacingAndGlyphs">Assessment Design</text>
    <text class="cond-light" x="326" y="214" font-size="38" textLength="406" lengthAdjust="spacingAndGlyphs">Onboarding Accessibility</text>

    <text class="cond-regular" x="12" y="268" font-size="42" textLength="240" lengthAdjust="spacingAndGlyphs">Learning Paths</text>
    <text class="cond-light" x="266" y="268" font-size="38" textLength="466" lengthAdjust="spacingAndGlyphs">Simulations Authoring Tools</text>

    <text class="wide-light" x="12" y="328" font-size="54" textLength="720" lengthAdjust="spacingAndGlyphs">Performance Support</text>

    <text class="cond-light" x="12" y="374" font-size="38" textLength="290" lengthAdjust="spacingAndGlyphs">Knowledge Checks</text>
    <text class="wide-light" x="316" y="374" font-size="36" textLength="416" lengthAdjust="spacingAndGlyphs">Storytelling</text>

    <text class="cond-bold" x="12" y="414" font-size="40" textLength="380" lengthAdjust="spacingAndGlyphs">Microlearning Modules</text>
    <text class="cond-light" x="404" y="414" font-size="38" textLength="328" lengthAdjust="spacingAndGlyphs">Virtual Training</text>
  </svg>
</section>

</body>
</html>
```